Create modern and sleek business card for luxury real estate company

We're a "boutique" real estate office looking for a design that gets across a highly modern luxury brand. Blacks and whites are probably the best colors unless we try a silver foil for the logo. I've attached a version of our current logo here. I'd like to swap out the current font on there with Gotham Light Regular.

I'm looking to have one side of the card have the logo with the space for our agents info on the other side.

Target Market(s)

Young professionals in a "luxury" headspace

Industry/Entity Type

Real estate

Contact Information for Business Card

A place for agent name, cell number, website. The slogan "Simply Rethinking Real Estate".

Font styles to use
Other font styles liked:
• Gotham Regular

Colors

Designer to choose only greyscale colors for use in the design.

Requirements
Must have
• Matte black as the background color. Clean lines and use of contrast. A specific design aspect that will use silver foil.
Nice to have
• Up in the air on integrating a QR code
Should not have
• Any houses or other real estate related design (ex: a clip art house)

```html
<!DOCTYPE html>
<html lang="en">
<head>
<meta charset="utf-8">
<title>Halden Realty — Business Card</title>
<link href="https://fonts.googleapis.com/css2?family=Montserrat:wght@300;400;600&display=swap" rel="stylesheet">
<style>
  :root {
    --stage: #1a1a1a;
    --card-white: #ffffff;
    --card-black: #151515;
    --ink: #111111;
    --ink-soft: #8a8a8a;
    --rule: #555555;
    --silver: #d9d9d9;
    --pattern-a: #1f1f1f;
    --pattern-b: #2a2a2a;
  }
  * { box-sizing: border-box; margin: 0; padding: 0; }
  html, body {
    width: 1200px; height: 900px; overflow: hidden;
    background: var(--stage);
    font-family: "Montserrat", sans-serif;
  }
  .stage {
    width: 1200px; height: 900px;
    display: flex; flex-direction: column;
    align-items: center; justify-content: center; gap: 56px;
  }
  .card {
    position: relative;
    width: 588px; height: 336px;
    border-radius: 18px;
    overflow: hidden;
    box-shadow: 0 14px 40px rgba(0,0,0,.55);
  }
  /* Front */
  .card--front { background: var(--card-white); color: var(--ink); }
  .brand {
    position: absolute; display: flex; align-items: center; gap: 12px;
  }
  .brand__mark {
    width: 50px; height: 50px; border-radius: 50%;
    border: 2px solid currentColor; flex: none;
  }
  .brand__name {
    font-weight: 400; letter-spacing: .12em; line-height: 1.05;
    text-transform: uppercase;
  }
  .card--front .brand { left: 220px; top: 52px; }
  .card--front .brand__name { font-size: 24px; }
  .rule { position: absolute; height: 1px; background: var(--rule); }
  .rule--top { left: 40px; top: 126px; width: 300px; }
  .rule--bottom { left: 300px; top: 286px; width: 250px; }
  .contact {
    position: absolute; left: 40px; top: 144px;
    list-style: none; font-size: 12.5px; font-weight: 300;
    color: var(--ink-soft); line-height: 1.65;
  }
  .contact li { display: flex; align-items: center; gap: 8px; }
  .contact svg { width: 11px; height: 11px; fill: var(--ink); flex: none; }
  .agent { position: absolute; left: 250px; top: 154px; }
  .agent__name { font-size: 17px; font-weight: 600; letter-spacing: .04em; text-transform: uppercase; }
  .agent__title { font-size: 12.5px; font-weight: 300; color: var(--ink-soft); margin-top: 2px; }
  .address {
    position: absolute; right: 38px; top: 232px; text-align: right;
    font-size: 12.5px; font-weight: 300; color: var(--ink-soft); line-height: 1.5;
  }
  /* Back */
  .card--back { background: var(--card-black); color: var(--silver); }
  .card__pattern {
    position: absolute; inset: 0;
    background: linear-gradient(135deg, var(--pattern-b), var(--pattern-a) 60%, var(--card-black));
  }
  .card--back .brand { right: 60px; top: 132px; }
  .card--back .brand__name { font-size: 22px; }
</style>
</head>
<body>
<main class="stage">
  <section class="card card--front" aria-label="Card front">
    <div class="brand">
      <span class="brand__mark"></span>
      <span class="brand__name">Halden<br>Realty</span>
    </div>
    <div class="rule rule--top"></div>
    <ul class="contact">
      <li><svg viewBox="0 0 24 24"><path d="M6.6 10.8a15.1 15.1 0 0 0 6.6 6.6l2.2-2.2a1 1 0 0 1 1-.25 11.4 11.4 0 0 0 3.6.57 1 1 0 0 1 1 1V20a1 1 0 0 1-1 1A17 17 0 0 1 3 4a1 1 0 0 1 1-1h3.5a1 1 0 0 1 1 1c0 1.25.2 2.45.57 3.57a1 1 0 0 1-.25 1z"/></svg>(555) 014-2290</li>
      <li><svg viewBox="0 0 24 24"><path d="M2 5h20v14H2zm2 2v.5l8 5 8-5V7l-8 5z"/></svg>info@haldenrealty.com</li>
      <li><svg viewBox="0 0 24 24"><path d="M12 2a10 10 0 1 0 0 20 10 10 0 0 0 0-20zm6.9 9h-3a15 15 0 0 0-1.3-5.7A8 8 0 0 1 18.9 11zM12 4.1c.9 1.3 1.7 3.7 1.9 6.9h-3.8c.2-3.2 1-5.6 1.9-6.9zM9.4 5.3A15 15 0 0 0 8.1 11h-3a8 8 0 0 1 4.3-5.7zM5.1 13h3a15 15 0 0 0 1.3 5.7A8 8 0 0 1 5.1 13zm6.9 6.9c-.9-1.3-1.7-3.7-1.9-6.9h3.8c-.2 3.2-1 5.6-1.9 6.9zm2.6-1.2a15 15 0 0 0 1.3-5.7h3a8 8 0 0 1-4.3 5.7z"/></svg>www.haldenrealty.com</li>
    </ul>
    <div class="agent">
      <h1 class="agent__name">Adrian Cole</h1>
      <p class="agent__title">Founder &amp; CEO</p>
    </div>
    <address class="address">41 Linden Row Suite 120<br>Sample City, Country</address>
    <div class="rule rule--bottom"></div>
  </section>

  <section class="card card--back" aria-label="Card back">
    <div class="card__pattern" role="img" aria-label="Tone-on-tone repeating brand emblem pattern in spot gloss on matte black"></div>
    <div class="brand">
      <span class="brand__mark"></span>
      <span class="brand__name">Halden<br>Realty</span>
    </div>
  </section>
</main>
</body>
</html>
```